Corvane Paintless Dent Removal

Our company works on vehicles removing dents using a highly skilled trade which the metal is massaged out with special tools without disturbing the original paint, hence paintless dent removal. Besides keeping the paint and metal original its also very environmentally friendly since no paint or toxic fillers are used. Also we we are one of the most experienced companies in the business with 25 years

Target Market(s)

Retail Automobile consumers, Auto Dealerships and Auto Body Shops

Industry/Entity Type

Auto Repair

Contact Information for Business Card

Dale Hollister
PO Box 518 Brookmere, NY 11962
631-555-0148
corvanepdr@mailbox-example.com
website corvanepdr.example
youtube corvane paintless dent removal
25 years of experience removing Dents, Dings and Hail Damage

Font styles to use
Serif
Sans Serif

Colors

Designer to choose colors to be used in the design.

Requirements
Must have
• I do like things that are simple but classy and somewhat bold, also I like my logo so that should be somewhat important

```html
<!DOCTYPE html>
<html lang="en">
<head>
<meta charset="utf-8">
<title>Corvane Paintless Dent Removal – Business Card</title>
<link href="https://fonts.googleapis.com/css2?family=Roboto:wght@400;500&family=Roboto+Condensed:wght@700&display=swap" rel="stylesheet">
<style>
  :root {
    --lime: #76c31a;
    --navy: #13294f;
    --paper: #fbfbfb;
    --ink: #2a3b5e;
    --gold: #d6a532;
    --stage: #e9e9e6;
    --white: #ffffff;
    --seal: #1b1b1b;
  }
  * { margin: 0; padding: 0; box-sizing: border-box; }
  html, body { width: 1200px; height: 911px; overflow: hidden; }
  body {
    background: var(--stage);
    font-family: "Roboto", Arial, sans-serif;
    position: relative;
  }
  .card {
    position: absolute;
    top: 301px;
    width: 540px;
    height: 309px;
    overflow: hidden;
    box-shadow: 0 6px 20px rgba(0,0,0,.18);
  }
  .card-front { left: 40px; background: var(--paper); }
  .card-back { left: 620px; background: var(--lime); }
  .card-shapes { position: absolute; inset: 0; width: 100%; height: 100%; }

  .brand {
    position: absolute;
    left: 110px;
    top: 52px;
    display: flex;
    align-items: center;
    gap: 10px;
  }
  .brand-dot {
    width: 22px; height: 22px;
    border-radius: 50%;
    background: var(--lime);
  }
  .brand-name {
    font-family: "Roboto Condensed", Arial, sans-serif;
    font-weight: 700;
    color: var(--navy);
    line-height: 1.05;
    font-size: 24px;
    text-transform: uppercase;
  }
  .brand-name small { display: block; font-size: 16px; text-transform: none; }

  .contact {
    position: absolute;
    left: 118px;
    top: 146px;
    color: var(--ink);
    font-size: 12.5px;
    line-height: 1.75;
    white-space: nowrap;
  }
  .contact-name {
    font-family: "Roboto Condensed", Arial, sans-serif;
    font-weight: 700;
    font-size: 15px;
    color: var(--navy);
    text-transform: uppercase;
    margin-bottom: 8px;
  }

  .back-name {
    position: absolute;
    left: 44px;
    top: 44px;
    color: var(--white);
    font-family: "Roboto Condensed", Arial, sans-serif;
    font-weight: 700;
    font-size: 42px;
    line-height: 1;
    text-transform: uppercase;
  }
  .back-name small { display: block; font-size: 20px; text-transform: none; margin-top: 4px; }
  .back-web {
    position: absolute;
    left: 46px;
    top: 128px;
    color: var(--white);
    font-size: 13px;
    letter-spacing: 2px;
  }
  .years-seal {
    position: absolute;
    right: 30px;
    top: 26px;
    width: 58px; height: 58px;
    border-radius: 50%;
    background: var(--seal);
    border: 3px solid var(--gold);
    color: var(--gold);
    display: flex; flex-direction: column;
    align-items: center; justify-content: center;
    font-family: "Roboto Condensed", Arial, sans-serif;
    font-weight: 700;
    line-height: 1;
  }
  .years-seal b { font-size: 22px; }
  .years-seal span { font-size: 8px; letter-spacing: 1px; }
</style>
</head>
<body>

  <section class="card card-front" aria-label="Business card front">
    <svg class="card-shapes" viewBox="0 0 540 309" aria-hidden="true">
      <path d="M505 0 H540 V309 H472 C496 220 510 110 505 0 Z" fill="var(--navy)"/>
      <path d="M0 150 C18 230 70 290 150 309 H0 Z" fill="var(--lime)"/>
    </svg>
    <div class="brand">
      <span class="brand-dot"></span>
      <div class="brand-name">Corvane<small>Paintless Dent Removal</small></div>
    </div>
    <div class="contact">
      <div class="contact-name">Dale Hollister</div>
      <div>P. 631-555-0148 &nbsp;E. corvanepdr@mailbox-example.com</div>
      <div>W. corvanepdr.example &nbsp;YT. corvane paintless dent removal</div>
      <div>PO Box 518, Brookmere, NY 11962</div>
    </div>
  </section>

  <section class="card card-back" aria-label="Business card back">
    <div class="back-name">Corvane<small>Paintless Dent Removal</small></div>
    <div class="back-web">corvanepdr.example</div>
    <div class="years-seal"><b>25</b><span>YEARS</span></div>
  </section>

</body>
</html>
```